Velmora Consulting Business

** Please add the content information from my old business card
1. I would like to see a two sided business card with both options with the 1st Option--Tallow Spire-new WHITE BACKGROUND LOGO
2 nd Option-Tallow Spire - new BLACK- Background Logo
3rd -Option a business card with my Photo on the card
Please add the new word to the card information:
EXECUTION
AS THE OWNER'S REP
WE AIM TO ACHIEVE YOUR
INFRASTRUCTURE VISION with
OUR SPECIALIZATION & EXECUTION in:

FUNDING Planning
BUSINESS Planning
INFRASTRUCTURE Planning
PROJECT Management
Since 2012
_____________________________________________________________________
I want to get spot uv raised printing. I was liking a a nice rich white linen paper stock with black writing & NOT A COLORED CARD other than a variety of white or black cards concept

```html
<!DOCTYPE html>
<html lang="en">
<head>
<meta charset="utf-8">
<title>Velmora Consulting – Business Card</title>
<link href="https://fonts.googleapis.com/css2?family=Open+Sans:wght@400;600;700;800&display=swap" rel="stylesheet">
<style>
  :root {
    --stage: #2a2a2c;
    --paper: #ecebf0;
    --ink: #1a1a1a;
    --card-black: #141414;
    --white: #ffffff;
    --accent-red: #e3152f;
    --muted: #9a9aa2;
  }
  * { box-sizing: border-box; margin: 0; padding: 0; }
  html, body { width: 1200px; height: 866px; overflow: hidden; }
  body {
    background: var(--stage);
    font-family: "Open Sans", Arial, sans-serif;
    position: relative;
  }
  .card {
    position: absolute;
    top: 278px;
    width: 540px;
    height: 310px;
    border-radius: 3px;
  }
  .card--front { left: 40px; background: var(--paper); color: var(--ink); }
  .card--back { left: 620px; background: var(--card-black); color: var(--white); }

  /* Brand name set as plain text */
  .brand {
    font-weight: 800;
    letter-spacing: -0.5px;
    line-height: 1;
  }
  .brand__name { display: block; font-size: 44px; }
  .brand__sub {
    display: block;
    font-size: 13px;
    letter-spacing: 11px;
    margin-top: 6px;
  }
  .brand__mark {
    display: inline-block;
    width: 10px; height: 10px;
    background: currentColor;
    margin-left: 8px;
    vertical-align: top;
  }

  .card--front .brand {
    position: absolute;
    right: 36px;
    top: 48px;
    text-align: right;
  }
  .contact {
    position: absolute;
    right: 36px;
    top: 150px;
    text-align: right;
  }
  .contact__name { font-size: 19px; font-weight: 700; letter-spacing: 0.3px; }
  .contact__role {
    font-size: 12px; color: var(--accent-red);
    letter-spacing: 0.6px; margin-top: 2px;
  }
  .contact__lines { list-style: none; margin-top: 12px; font-size: 14px; line-height: 1.45; }
  .contact__lines li { display: flex; justify-content: flex-end; align-items: center; gap: 7px; }
  .contact__lines svg { width: 12px; height: 12px; fill: var(--ink); }
  .contact__city { font-size: 14px; margin-top: 10px; letter-spacing: 0.3px; }
  .contact__city .dot { color: var(--accent-red); }

  .services {
    position: absolute;
    left: 30px;
    top: 40px;
    font-size: 12px;
    line-height: 1.35;
    text-transform: none;
  }
  .services__pitch { letter-spacing: 0.2px; }
  .services__list { list-style: none; margin-top: 10px; }
  .services__list li { display: flex; align-items: center; gap: 7px; }
  .services__list li::before {
    content: ""; width: 6px; height: 6px; background: var(--accent-red);
  }
  .services__since { color: var(--accent-red); margin-top: 6px; }

  .card--back .brand {
    position: absolute;
    right: 30px;
    bottom: 54px;
    text-align: right;
  }
  .card--back .brand__name { font-size: 36px; }
  .card--back .brand__sub { font-size: 11px; letter-spacing: 9px; }
</style>
</head>
<body>

  <section class="card card--front" aria-label="Card front">
    <div class="brand">
      <span class="brand__name">Velmora<span class="brand__mark"></span></span>
      <span class="brand__sub">CONSULTING</span>
    </div>
    <div class="contact">
      <p class="contact__name">Renata Colwell-Ashby</p>
      <p class="contact__role">CEO / LEAD PROJECT MANAGER</p>
      <ul class="contact__lines">
        <li>867.555.0142
          <svg viewBox="0 0 12 12"><path d="M2.5 1l2 2.3-1 1.2a7 7 0 0 0 4 4l1.2-1 2.3 2-1.2 1.5C5.5 11 1 6.5 1 2.2z"/></svg>
        </li>
        <li>renata@velmora.ca
          <svg viewBox="0 0 12 12"><path d="M0 2h12v8H0zm1 1v.4l5 3.2 5-3.2V3z"/></svg>
        </li>
        <li>www.velmora.ca
          <svg viewBox="0 0 12 12"><circle cx="6" cy="6" r="5" fill="none" stroke="#1a1a1a" stroke-width="1.2"/><path d="M1 6h10M6 1v10" stroke="#1a1a1a" stroke-width="1"/></svg>
        </li>
      </ul>
      <p class="contact__city">Harrow Bay NT <span class="dot">•</span> Linden Falls NB</p>
    </div>
  </section>

  <section class="card card--back" aria-label="Card back">
    <div class="services">
      <p class="services__pitch">EXECUTION<br>AS THE OWNER'S REP<br>WE AIM TO ACHIEVE YOUR<br>INFRASTRUCTURE VISION with<br>OUR SPECIALIZATION &amp; EXECUTION in:</p>
      <ul class="services__list">
        <li>FUNDING Planning</li>
        <li>BUSINESS Planning</li>
        <li>INFRASTRUCTURE Planning</li>
        <li>PROJECT Management</li>
      </ul>
      <p class="services__since">Since 2012</p>
    </div>
    <div class="brand">
      <span class="brand__name">Velmora<span class="brand__mark"></span></span>
      <span class="brand__sub">CONSULTING</span>
    </div>
  </section>

</body>
</html>
```